Borvik Media - Amazing Homepage

We would like to build an amazing homepage for our site. We will need it built in HTM5, so it works across devices and would like it to parallax scroll , so it looks amazing.
We are a digital media agency, that has recently launched. Our old site is self build through one of the standard web build sites. We will be hosting our new site independently.
This is our old site - www.borvik-media.example
The new site only really needs one scrolling page to explain what we do and have our contact details at the bottom.
We have a place to host it, once designed. So we can share with the final design for you to upload.
Attached are:
Brief
Logos and artwork
Our PowerPoint template to give you an idea of colours

```html
<!DOCTYPE html>
<html lang="en">
<head>
<meta charset="utf-8">
<title>Borvik Media</title>
<link rel="stylesheet" href="https://fonts.googleapis.com/css2?family=Raleway:wght@300;400;500;600&family=Open+Sans:wght@400;600;700&display=swap">
<style>
:root{
  --red:#7d1515;
  --red-nav:#a41c1c;
  --gold:#d5a11b;
  --gold-btn:#e3a21a;
  --charcoal:#3d3d3d;
  --charcoal-deep:#393634;
  --footer:#262626;
  --ink:#4a4a4a;
  --white:#ffffff;
  --grey-btn:#e1e1e1;
  --card-label:#e9e9e9;
}
*{margin:0;padding:0;box-sizing:border-box}
html,body{width:1200px;height:3622px;overflow:hidden}
body{position:relative;background:var(--white);font-family:"Open Sans",Arial,sans-serif;color:var(--ink)}
.h{font-family:"Raleway",Arial,sans-serif}
section,header,nav,footer{position:absolute;left:0;width:1200px}
.abs{position:absolute}
.center{text-align:center;left:0;width:1200px}
.notch{position:absolute;left:580px;top:0;width:0;height:0;border-left:20px solid transparent;border-right:20px solid transparent;border-top:16px solid var(--white)}

/* header */
.site-header{top:0;height:133px}
.brand-name{font-family:"Raleway",sans-serif;font-weight:500;color:var(--ink);line-height:1;white-space:nowrap}
.site-header .brand-name{position:absolute;left:181px;top:34px;font-size:30px;letter-spacing:3px}
.btn{position:absolute;display:block;text-align:center;font-size:12px;font-weight:600;line-height:34px;height:34px;border-radius:3px}
.btn-login{left:821px;top:75px;width:101px;background:var(--gold-btn);color:var(--white)}
.btn-register{left:929px;top:75px;width:99px;background:var(--grey-btn);color:var(--ink)}

/* nav */
.main-nav{top:133px;height:43px;background:linear-gradient(#b32323,var(--red-nav) 50%,#8c1616)}
.main-nav a{position:absolute;top:0;line-height:43px;color:var(--white);font-size:13px;text-decoration:none;font-weight:600;transform:translateX(-50%)}

/* hero */
.hero{top:176px;height:529px}
.hero-photo{position:absolute;inset:0;background:radial-gradient(ellipse at 50% 55%,#3d6d8c 0%,#1d2d3d 40%,#0e0f12 80%)}
.hero-title{position:absolute;left:0;width:1200px;text-align:center;color:var(--white);font-family:"Raleway",sans-serif;font-weight:400}
.hero-arrow{position:absolute;top:196px;width:66px;height:66px;border-radius:50%;background:var(--white)}

/* clarity */
.clarity{top:705px;height:340px}
.clarity h2{position:absolute;left:169px;top:44px;font-size:29px;font-weight:400;color:#9b1b1b}
.clarity ul{position:absolute;left:175px;top:100px;list-style:none;width:520px}
.clarity li{position:relative;padding-left:22px;font-size:12px;line-height:17px;margin-bottom:10px;color:#555}
.clarity li::before{content:"";position:absolute;left:2px;top:3px;width:8px;height:4px;border-left:2px solid #8bb32a;border-bottom:2px solid #8bb32a;transform:rotate(-45deg)}
.clarity .motto{position:absolute;left:185px;top:258px;font-size:12px;color:#555}
.bulb{position:absolute;left:730px;top:30px;width:220px;height:265px;border-radius:50%;background:radial-gradient(ellipse,#f3c94a,#e97a5a 40%,#6bb4d8 65%,#ffffff 85%)}

/* gold */
.values{top:1045px;height:452px;background:var(--gold)}
.values h2{top:62px;font-size:30px;font-weight:400;color:var(--white);line-height:42px}
.values p{top:150px;font-size:9.5px;color:#fff6df;line-height:13px}
.card{position:absolute;top:220px;width:347px;height:174px;background:var(--card-label)}
.card-photo{height:130px}
.card-label{text-align:center;font-family:"Raleway",sans-serif;font-weight:600;font-size:17px;line-height:44px;color:#2c2c2c}

/* coup */
.coup{top:1497px;height:422px}
.coup h2{position:absolute;left:169px;top:82px;font-size:29px;font-weight:400;color:#444}
.coup .sub{position:absolute;left:169px;top:126px;width:600px;font-size:18px;line-height:30px;color:#777;font-family:"Raleway",sans-serif}
.coup .body{position:absolute;left:169px;top:203px;width:510px;font-size:10px;line-height:14px;color:#666}
.coup .body + .body{top:255px}
.crate{position:absolute;left:785px;top:125px;width:224px;height:181px;background:linear-gradient(160deg,#d9d2c4,#8c8272 60%,#5a5248)}

/* quiet coup */
.quiet{top:1919px;height:403px;background:var(--charcoal)}
.quiet h2{top:92px;font-size:34px;font-weight:400;color:var(--white)}
.quiet p{font-size:10px;line-height:14px;color:#d8d8d8}
.btn-more{left:526px;top:263px;width:111px;height:30px;line-height:30px;background:var(--gold-btn);color:var(--white);font-size:11px}

/* services */
.services{top:2322px;height:413px;background:var(--red)}
.services .notch{border-top-color:var(--charcoal)}
.services h2{top:58px;font-size:30px;font-weight:400;color:var(--white);line-height:40px}
.services .lead{top:150px;font-size:12px;color:#e9c7c7}
.service{position:absolute;top:210px;width:160px;margin-left:-80px;text-align:center;color:var(--white);font-size:14px;font-weight:600}
.service svg{display:block;margin:0 auto 14px;height:52px}
.services .board{top:320px;font-size:12px;color:#d9a6a6}

/* clients */
.clients{top:2735px;height:471px}
.clients h2{top:42px;font-size:30px;font-weight:400;color:#5a5a5a}
.clients .sub{top:84px;font-size:19px;line-height:31px;color:#777;font-family:"Raleway",sans-serif}
.clients .mid-brand{top:184px;font-size:20px;letter-spacing:3px}
.clients h3{top:258px;font-size:20px;font-weight:400;color:#8a8a8a}
.client-row{position:absolute;left:280px;width:660px;display:flex;justify-content:space-between}
.client{display:flex;align-items:center;gap:4px;font-size:9px;font-weight:700;color:#555;line-height:11px;white-space:nowrap}
.client i{flex:none;width:10px;height:10px;background:#b42a2a;display:block}

/* contact */
.contact{top:3206px;height:347px;background:var(--charcoal-deep)}
.contact h2{top:106px;font-size:26px;font-weight:400;color:var(--white)}
.contact .sub{top:142px;font-size:19px;color:#e0e0e0;font-family:"Raleway",sans-serif}
.contact .info{font-size:13px;color:#bcbcbc}
.socials{position:absolute;left:551px;top:242px;display:flex;gap:10px}
.socials span{width:24px;height:24px;border-radius:50%;background:var(--white);display:block}

/* footer */
.site-footer{top:3553px;height:69px;background:var(--footer)}
.site-footer p{position:absolute;left:169px;top:26px;font-size:11px;color:#9a9a9a}
</style>
</head>
<body>

<header class="site-header">
  <div class="brand-name">BORVIK MEDIA</div>
  <a class="btn btn-login">LOGIN</a>
  <a class="btn btn-register">REGISTER</a>
</header>

<nav class="main-nav">
  <a style="left:249px">HOME</a>
  <a style="left:362px">ABOUT US</a>
  <a style="left:526px">WHAT WE CAN OFFER</a>
  <a style="left:686px">SERVICE</a>
  <a style="left:801px">SUPPORT</a>
  <a style="left:925px">CONTACT</a>
</nav>

<section class="hero">
  <div class="hero-photo" role="img" aria-label="Hands holding a tablet with a laptop, phone and network of digital icons rising from it"></div>
  <div class="hero-title" style="top:168px;font-size:34px">Got the feeling your</div>
  <div class="hero-title" style="top:206px;font-size:62px">Digital Marketing</div>
  <div class="hero-title" style="top:288px;font-size:32px">just isn’t quite ‘there’?</div>
  <div class="hero-arrow" style="left:76px">
    <svg width="66" height="66" viewBox="0 0 66 66"><path d="M37 22 L26 33 L37 44" fill="none" stroke="#333" stroke-width="3"/></svg>
  </div>
  <div class="hero-arrow" style="left:1058px">
    <svg width="66" height="66" viewBox="0 0 66 66"><path d="M29 22 L40 33 L29 44" fill="none" stroke="#333" stroke-width="3"/></svg>
  </div>
</section>

<section class="clarity">
  <h2 class="h">We keep fighting to give you clarity by:</h2>
  <ul>
    <li>Creating a singular view of your digital eco system</li>
    <li>Reviewing how and why your money is being spent where it is</li>
    <li>Profiling your customers. Who doesn’t have 1000’s of different customers with different motivations, interests and value to the brand?</li>
    <li>Finding the best digital channels to communicate with them Because everything is changing every day...exciting isn’t it!</li>
  </ul>
  <p class="motto">Never stop, never settle, always improve. Be amazing.</p>
  <div class="bulb" role="img" aria-label="Light bulb illustration made of colourful speech bubbles"></div>
</section>

<section class="values">
  <span class="notch"></span>
  <h2 class="abs center h">Every client deserves amazing work,<br>regardless of the brand, it’s all real money</h2>
  <p class="abs center">We shape honest campaigns around real goals, measure every pound spent and share the numbers openly, so each brand we touch grows with purpose and lasting results.<br>Clear plans, steady reporting and creative ideas that earn attention from the people who matter most.</p>
  <div class="card" style="left:237px">
    <div class="card-photo" role="img" aria-label="Photo of colourful glass marbles" style="background:linear-gradient(135deg,#6fa7d8,#e4d27a 40%,#d2553f 70%,#3c7d4f)"></div>
    <div class="card-label">MARBLES</div>
  </div>
  <div class="card" style="left:618px">
    <div class="card-photo" role="img" aria-label="Photo of a businessman holding a football" style="background:linear-gradient(160deg,#4a4f57,#1e2127 60%,#c9c9c9)"></div>
    <div class="card-label">FOOTBALL STICKERS</div>
  </div>
</section>

<section class="coup">
  <span class="notch" style="border-top-color:var(--gold)"></span>
  <h2 class="h">It’s time to start a coup...there are too many</h2>
  <p class="sub">large agency networks, too few agencies being transparent, too many putting quality of work second to income</p>
  <p class="body">Most agencies hide behind jargon and long retainers. We prefer plain talk, fair fees and work that speaks for itself, measured against the goals you set with us from day one.</p>
  <p class="body">We answer quickly, test often and share what we learn, so your budget always works harder than before.</p>
  <div class="crate" role="img" aria-label="Old wooden crate"></div>
</section>

<section class="quiet">
  <span class="notch"></span>
  <h2 class="abs center h">Well, a very quiet coup.</h2>
  <p class="abs center" style="top:145px;padding:0 320px">We are not loud about it. We simply do the work properly, report it clearly and keep improving, month after month, for every client we partner with.</p>
  <p class="abs center" style="top:183px;padding:0 300px">Our team blends search, social, display and data skills under one roof, so strategy and delivery stay joined up and nothing gets lost between specialists along the way.</p>
  <a class="btn btn-more">READ MORE</a>
</section>

<section class="services">
  <span class="notch"></span>
  <h2 class="abs center h">We’ve yet to come across a client that wants to<br>shrink...making us specialists in delivering growth!</h2>
  <p class="abs center lead">We’ve been optimising our digital knowledge for over 20 years and we genuinely know what we are talking about</p>

  <div class="service" style="left:212px">
    <svg viewBox="0 0 52 52" width="52"><circle cx="22" cy="14" r="10" fill="none" stroke="#fff" stroke-width="2"/><path d="M20 14 v20 l-6-5 -3 3 10 12 h14 l4-14 -12-4 v-12z" fill="#fff"/></svg>PPC</div>
  <div class="service" style="left:314px">
    <svg viewBox="0 0 52 52" width="52"><rect x="6" y="8" width="36" height="28" fill="none" stroke="#fff" stroke-width="3"/><rect x="12" y="16" width="10" height="10" fill="#fff"/><circle cx="36" cy="36" r="8" fill="none" stroke="#fff" stroke-width="3"/><path d="M42 42 l7 7" stroke="#fff" stroke-width="4"/></svg>SEO</div>
  <div class="service" style="left:422px">
    <svg viewBox="0 0 52 52" width="52"><rect x="4" y="6" width="44" height="30" rx="2" fill="none" stroke="#fff" stroke-width="3"/><rect x="22" y="36" width="8" height="8" fill="#fff"/><rect x="14" y="44" width="24" height="4" fill="#fff"/></svg>DISPLAY</div>
  <div class="service" style="left:555px">
    <svg viewBox="0 0 60 52" width="60"><circle cx="18" cy="16" r="8" fill="#fff"/><circle cx="42" cy="16" r="8" fill="#fff"/><circle cx="30" cy="20" r="9" fill="#fff" stroke="var(--red)" stroke-width="2"/><path d="M4 46 q14-22 28 0z M28 46 q14-22 28 0z M14 48 q16-24 32 0z" fill="#fff"/></svg>PAID SOCIAL</div>
  <div class="service" style="left:744px">
    <svg viewBox="0 0 52 52" width="52"><rect x="6" y="4" width="40" height="12" fill="#fff"/><rect x="6" y="20" width="40" height="12" fill="#fff"/><rect x="6" y="36" width="40" height="12" fill="#fff"/><circle cx="38" cy="10" r="2" fill="var(--red)"/><circle cx="38" cy="26" r="2" fill="var(--red)"/><circle cx="38" cy="42" r="2" fill="var(--red)"/></svg>DATA MANAGEMENT</div>
  <div class="service" style="left:927px">
    <svg viewBox="0 0 52 52" width="52"><rect x="8" y="6" width="36" height="44" rx="2" fill="none" stroke="#fff" stroke-width="3"/><rect x="18" y="2" width="16" height="8" fill="#fff"/><path d="M15 22h22M15 30h22M15 38h22" stroke="#fff" stroke-width="3"/></svg>ATTRIBUTION</div>

  <p class="abs center board">Operating at board level in top 10 digital agencies</p>
</section>

<section class="clients">
  <span class="notch" style="border-top-color:var(--red)"></span>
  <h2 class="abs center h">Happily, we smash it for all our clients,</h2>
  <p class="abs center sub">with an average of 35%&nbsp; improvement in performance within the first<br>quarter of working with us</p>
  <div class="abs center brand-name mid-brand">BORVIK MEDIA</div>
  <h3 class="abs center h">Our Clients</h3>
  <div class="client-row" style="top:328px">
    <span class="client"><i></i>Arvona</span>
    <span class="client"><i></i>Tidebridge</span>
    <span class="client"><i></i>Norrow</span>
    <span class="client"><i></i>Plumet</span>
    <span class="client"><i></i>Kestrel Scaffolds</span>
    <span class="client"><i></i>Quillan</span>
    <span class="client"><i></i>Lumetra</span>
    <span class="client"><i></i>Propworks</span>
  </div>
  <div class="client-row" style="top:400px">
    <span class="client"><i></i>Halden</span>
    <span class="client"><i></i>Corvane</span>
    <span class="client"><i></i>Stellix</span>
    <span class="client"><i></i>Brightmoor</span>
    <span class="client"><i></i>Vellum Art</span>
    <span class="client"><i></i>Oakhurst</span>
    <span class="client"><i></i>Pennard</span>
    <span class="client"><i></i>Thistlecombe</span>
  </div>
</section>

<section class="contact">
  <span class="notch"></span>
  <h2 class="abs center h">If you are still reading our rant then get in</h2>
  <p class="abs center sub">touch / follow us / let’s go for a coffee</p>
  <p class="abs center info" style="top:186px">Our address is 14 Harlow Lane, London, EC2 9QT</p>
  <p class="abs center info" style="top:212px">contact@borvik-media.example</p>
  <div class="socials"><span></span><span></span><span></span><span></span></div>
</section>

<footer class="site-footer">
  <p>© 2014 Company Name&nbsp; All right reserved&nbsp; Term of Use</p>
</footer>

</body>
</html>
```